IRON PEAK TRAINING- Shooting Range!!!And virtual shooting range!!!

We are looking to do a clean cut web page for shooting range. We have indoor shooting simulator, retail store that sales accessories and pistols, rifles and shot guns. We are membership based for indoor shooting range Only and virtual shooting is open to public as well as retail store. We also specialize in shooting training classes and CWP classes.
Updates

Thank you for your patience. We are working with a busy travel schedule. We will be making final decisions tomorrow and moving forward with getting this launched. Regards, Gerald

Target Market(s)

Public and private entertainment

Industry/Entity Type

Training

Number of Pages Required

5+ page

Font styles to use
Sans Serif

Requirements
Must have
• Clean and easy approach we really like the website our friend has www.valormarkline.com please take a look at a lay out. We would like to also add onli member schedule that is available for shooting sections and that they can access and book them selvs.
Nice to have
• White, black, gray or red colors

```html
<!DOCTYPE html>
<html lang="en">
<head>
<meta charset="utf-8">
<title>Iron Peak Training – Shooting Range</title>
<link rel="stylesheet" href="https://fonts.googleapis.com/css2?family=Ropa+Sans&family=Signika:wght@400;600&family=Arimo:wght@400&family=Lato:wght@400&display=swap">
<style>
:root{
  --page:#ececea;
  --black:#000;
  --red:#de1c24;
  --red-dark:#b5141b;
  --grey:#6b6b6b;
  --grey-btn:#6e6e6e;
  --text:#8a8a8a;
  --white:#fff;
  --nav:#c9c9c9;
}
*{margin:0;padding:0;box-sizing:border-box}
html,body{width:1012px;height:1200px;overflow:hidden}
body{background:var(--page);position:relative;font-family:"Arimo",sans-serif;color:var(--text)}
.abs{position:absolute}

.site-header{left:50px;top:51px;width:911px;height:106px;background:var(--black)}
.brand{left:22px;top:28px;display:flex;align-items:center;gap:8px}
.brand-dot{width:22px;height:22px;border-radius:50%;background:var(--red)}
.brand-name{font-family:"Ropa Sans",sans-serif;font-size:21px;color:var(--white);letter-spacing:1px;line-height:1.05}
.main-nav{left:425px;top:0;height:106px;display:flex;font-family:"Ropa Sans",sans-serif;font-size:15.5px}
.main-nav a{color:var(--nav);text-decoration:none;display:flex;align-items:center;padding:0 13px}
.main-nav a.active{background:var(--red);color:var(--white);width:63px;justify-content:center;padding:0}

.hero{left:50px;top:160px;width:911px;height:336px;background:var(--black);box-shadow:0 6px 6px -4px rgba(0,0,0,.35)}
.hero-photo{left:0;top:0;width:911px;height:286px;background:radial-gradient(ellipse at 45% 40%,#b5784a 0%,#7a4220 45%,#3a1d0c 100%)}
.hero-arrow{top:145px;width:29px;height:36px;background:var(--red-dark);display:flex;align-items:center;justify-content:center}
.hero-caption{left:20px;top:286px;height:50px;display:flex;align-items:center;gap:10px;white-space:nowrap}
.hero-caption h2{font-family:"Ropa Sans",sans-serif;font-weight:400;font-size:19px;color:var(--red)}
.hero-caption p{font-family:"Ropa Sans",sans-serif;font-size:11px;color:#ddd}

.booking-title{left:200px;top:515px;font-family:"Ropa Sans",sans-serif;font-size:19px;color:var(--red)}
.booking-text{left:204px;top:545px;width:420px;font-family:"Ropa Sans",sans-serif;font-size:11px;line-height:13px;color:#999}
.btn-book{left:662px;top:518px;width:150px;height:46px;background:var(--grey-btn);color:var(--white);font-family:"Arimo",sans-serif;font-size:16px;display:flex;align-items:center;justify-content:center;box-shadow:0 2px 2px rgba(0,0,0,.3)}
.divider{left:50px;top:594px;width:911px;height:1px;background:#d2d2d2}

.feature{top:614px;width:215px}
.feature-photo{width:215px;height:141px;box-shadow:0 1px 3px rgba(0,0,0,.4)}
.feature h3{margin-top:12px;font-family:"Signika",sans-serif;font-weight:600;font-size:19px;color:#111;letter-spacing:-.3px}
.feature h3 span{color:var(--red);font-weight:400}
.feature p{margin-top:9px;font-size:10.5px;line-height:13.4px;text-align:justify;color:var(--text)}
.btn-more{display:inline-flex;margin-top:11px;width:65px;height:31px;background:var(--red);color:var(--white);font-size:12px;align-items:center;justify-content:center;box-shadow:0 2px 0 var(--red-dark)}

.site-footer{left:50px;top:914px;width:911px;height:192px;background:var(--black);color:var(--white)}
.footer-col{top:24px}
.footer-col h4{font-family:"Ropa Sans",sans-serif;font-weight:400;font-size:20px;margin-bottom:12px}
.footer-col li{list-style:none;font-family:"Lato",sans-serif;font-size:12px;line-height:18.6px}
.contact-row{display:flex;gap:9px;font-family:"Lato",sans-serif;font-size:11.5px;line-height:14px;margin-bottom:14px}
.contact-row svg{flex:none;margin-top:1px}
.news-text{font-size:11px;line-height:18px;color:#ddd;font-family:"Lato",sans-serif}
.news-input{margin-top:7px;width:153px;height:28px;background:var(--white);display:flex;align-items:center;gap:6px;padding-left:8px;font-size:10px;color:#777}
.news-btn{margin-top:10px;width:153px;height:28px;background:var(--grey-btn);display:flex;align-items:center;justify-content:center;font-size:12px;letter-spacing:.5px}
.social{display:flex;gap:8px;margin-left:-6px}
.social span{width:23px;height:23px;border-radius:50%;display:block}
.footer-brand{margin-top:30px;margin-left:0;display:flex;align-items:center;gap:6px;font-family:"Ropa Sans",sans-serif;font-size:14px;color:#aaa}
.footer-brand i{width:12px;height:12px;border-radius:50%;background:#888;display:block}
.bottom-bar{left:50px;top:1106px;width:911px;height:38px;background:var(--grey);box-shadow:0 6px 6px -4px rgba(0,0,0,.35)}
.copyright{right:21px;top:12px;font-family:"Lato",sans-serif;font-size:10.5px;color:var(--white)}
</style>
</head>
<body>

<header class="site-header abs">
  <div class="brand abs"><span class="brand-dot"></span><span class="brand-name">IRON PEAK<br>TRAINING</span></div>
  <nav class="main-nav abs">
    <a class="active" href="#">Home</a>
    <a href="#">About</a>
    <a href="#">Training Classes</a>
    <a href="#">Location</a>
    <a href="#">Store</a>
    <a href="#">Blog</a>
  </nav>
</header>

<section class="hero abs">
  <div class="hero-photo abs" role="img" aria-label="Photo of a silver and black pistol with cartridges on a wooden table"></div>
  <div class="hero-arrow abs" style="left:0">
    <svg width="8" height="12" viewBox="0 0 8 12"><path d="M6 1 1 6l5 5" fill="none" stroke="#fff" stroke-width="1.3"/></svg>
  </div>
  <div class="hero-arrow abs" style="right:0">
    <svg width="8" height="12" viewBox="0 0 8 12"><path d="M2 1l5 5-5 5" fill="none" stroke="#fff" stroke-width="1.3"/></svg>
  </div>
  <div class="hero-caption abs">
    <h2>Lorium Ipsum :</h2>
    <p>Nemo enim ipsam voluptatem quia voluptas sit aspernatur aut odit aut fugit, sed quia consequuntur magni dolores eos qui ratione voluptatem sequi nesciunt.</p>
  </div>
</section>

<h2 class="booking-title abs">We need online member bookings for shooting sessions.</h2>
<p class="booking-text abs">Nemo enim ipsam voluptatem quia voluptas sit aspernatur aut odit aut fugit, sed quia consequuntur magni dolores eos qui ratione voluptatem sequi nesciunt.</p>
<div class="btn-book abs">BOOK NOW</div>
<div class="divider abs"></div>

<article class="feature abs" style="left:51px">
  <div class="feature-photo" role="img" aria-label="Photo of rifles displayed on a retail store wall" style="background:linear-gradient(180deg,#8a8a86,#4c4c4a)"></div>
  <h3>PREMIUM <span>RETAIL STORE</span></h3>
  <p>Duis aute irure dolor in reprehenderit in voluptate velit esse cillum dolore eu fugiat nulla pariatur. Excepteur sint occaecat cupidatat non proident.</p>
  <span class="btn-more">MORE</span>
</article>
<article class="feature abs" style="left:286px">
  <div class="feature-photo" role="img" aria-label="Photo of two trainees in tactical gear aiming pistols" style="background:linear-gradient(180deg,#5a5e63,#2a2c2f)"></div>
  <h3>TRAINING <span>CLASSES</span></h3>
  <p>Duis aute irure dolor in reprehenderit in voluptate velit esse cillum dolore eu fugiat nulla pariatur. Excepteur sint occaecat cupidatat non proident.</p>
  <span class="btn-more">MORE</span>
</article>
<article class="feature abs" style="left:518px">
  <div class="feature-photo" role="img" aria-label="Photo of a shooter in camouflage aiming a rifle down a range" style="background:linear-gradient(135deg,#6f6a5c,#3c3d33 60%,#1f2020)"></div>
  <h3>CWP <span>CLASSES</span></h3>
  <p>Duis aute irure dolor in reprehenderit in voluptate velit esse cillum dolore eu fugiat nulla pariatur. Excepteur sint occaecat cupidatat non proident.</p>
  <span class="btn-more">MORE</span>
</article>
<article class="feature abs" style="left:749px">
  <div class="feature-photo" role="img" aria-label="Photo of an indoor shooting range lane with targets" style="background:linear-gradient(180deg,#d6d8d2,#8f928d)"></div>
  <h3>PREMIER <span>FACILITY</span></h3>
  <p>Duis aute irure dolor in reprehenderit in voluptate velit esse cillum dolore eu fugiat nulla pariatur. Excepteur sint occaecat cupidatat non proident.</p>
  <span class="btn-more">MORE</span>
</article>

<footer class="site-footer abs">
  <div class="footer-col abs" style="left:42px">
    <h4>QUICK LINKS</h4>
    <ul style="margin-left:4px">
      <li>Home</li><li>About Us</li><li>Services</li><li>Testimonials</li><li>Career</li><li>Contact Us</li>
    </ul>
  </div>
  <div class="footer-col abs" style="left:268px">
    <h4>CONTACT INFO</h4>
    <div class="contact-row">
      <svg width="12" height="11" viewBox="0 0 12 11"><path d="M6 0 0 5h1.5v6h3.5V7.5h2V11h3.5V5H12z" fill="#fff"/></svg>
      <span>Company name<br>Unit 406, 4th Floor,<br>Lorem Ipsum is simply,<br>Sector-x, Ridgeford - 480210</span>
    </div>
    <div class="contact-row">
      <svg width="12" height="13" viewBox="0 0 12 13"><rect x="3" y="0.5" width="6" height="12" rx="1" fill="none" stroke="#fff"/><rect x="5" y="10" width="2" height="1" fill="#fff"/></svg>
      <span>Phone : 000-000-0000</span>
    </div>
    <div class="contact-row">
      <svg width="12" height="12" viewBox="0 0 12 12"><rect x="1" y="4" width="10" height="7" fill="#fff"/><rect x="3" y="1" width="6" height="3" fill="none" stroke="#fff"/></svg>
      <span>Fax : 000 - 000 - 0000</span>
    </div>
  </div>
  <div class="footer-col abs" style="left:510px">
    <h4>NEWSLETTER</h4>
    <p class="news-text" style="margin-left:3px">Sign up to receive the latest<br>updates</p>
    <div class="news-input" style="margin-left:3px">
      <svg width="10" height="8" viewBox="0 0 10 8"><rect x=".5" y=".5" width="9" height="7" fill="none" stroke="#888"/><path d="M.5.5 5 4.5 9.5.5" fill="none" stroke="#888"/></svg>
      Email id
    </div>
    <div class="news-btn" style="margin-left:3px">SUBSCRIBE</div>
  </div>
  <div class="footer-col abs" style="left:737px">
    <h4>FOLLOW US</h4>
    <div class="social">
      <span style="background:#3b5998"></span>
      <span style="background:#1da1f2"></span>
      <span style="background:#0e76a8"></span>
      <span style="background:#d34836"></span>
    </div>
    <div class="footer-brand"><i></i>IRON PEAK</div>
  </div>
</footer>

<div class="bottom-bar abs">
  <p class="copyright abs">© 2015.www.valormarkline.com. All rights reserved.</p>
</div>

</body>
</html>
```